Design my site www.brieflyledger.com

So here is what I am thinking in terms of design:

https://plenvo.com

https://www.skyluxair.com

http://kalvex.com/harbor-plaza-tower/

I want the theme to be white and blue (royal blue). I attached a paint picture of what I would like the site to look like in terms of placing the text. Generally, what I like about the sites above is that they are simple, you can navigate easily and have some kind of idea of what's going on by looking at the center (picture and motto). Let's establish a clear understanding of how the functional part of the site would look like. Please see the picture attached.

I want to keep it simple: On top would be the Name 'BRIEFLY ledger", somewhere to the right on top on the page would be 'Sign in" button.

In the center would be a picture (maybe a video) with the Motto (on top of it all in capital) OBSERVE NAVIGATE DECIDE and below would be the "sign up now"

Below the picture (like on kalvex.com site) or to the left on top of the page would be "About Us', "Press" "Contact Us' buttons.

Then once the user gets to his page his got 3 tabs " Press Headlines", "Events", " Briefings".

we would keep the same format I only have on the site, but separate for every Tab.

I do not want the user to get distracted. I also want him to be able to access the page though mobile phone and be able to get automatic updates just like Zorvan Pings without having to sign in daily.

The landing page must be minimalist yet with business/corporate feel where users can navigate easily and a "what you see is what you get" approach. You want an image or video (personally I prefer the video.. it does capture the users attention instantly, as long as it is an interesting video), with your taglines in it.

Sections available to public: About Us, Contact Us, Landing Page with Signup Option

Private: Public Sections + User Account Page, Tabs for (Events, Press Headlines, Briefings)

Target Market(s)

PR/media monitoring/diplomatic community

Coding

Coded - Design and coding required

Number of Pages Required

1 page

Font styles to use
Serif
Sans Serif

Colors
0255a3
ec1f27

Requirements
Must have
• a simple landing page, that is user friendly.
Nice to have
• a video with the explanation of how to navigate the site
Should not have
• too many colors, graphs etc.

```html
<!DOCTYPE html>
<html lang="en">
<head>
<meta charset="utf-8">
<title>BRIEFLY ledger</title>
<link rel="stylesheet" href="https://fonts.googleapis.com/css2?family=Montserrat:wght@600;700&family=Open+Sans:wght@400;600&display=swap">
<style>
:root{
  --blue:#2a8dc6;
  --blue-dark:#1f78ad;
  --text:#444;
  --muted:#666;
  --panel:#f5f5f5;
  --line:#e2e2e2;
  --footer:#f7f7f7;
  --white:#fff;
}
*{box-sizing:border-box;margin:0;padding:0}
html,body{width:1200px;height:896px;overflow:hidden;background:var(--white);font-family:"Open Sans",sans-serif;color:var(--text)}
.page{position:relative;width:1200px;height:896px}
.hero{position:absolute;left:0;top:0;width:1200px;height:257px;
  background:linear-gradient(180deg,#2b3a4d 0%,#3a4656 30%,#2a3038 65%,#1d2227 100%);
  border-top:2px solid #3aa0d8}
.brand{position:absolute;left:99px;top:39px;width:321px;height:57px;border:2px solid var(--white);
  display:flex;align-items:center;justify-content:center;font-family:"Montserrat",sans-serif;font-weight:700;
  font-size:30px;color:var(--white);letter-spacing:-0.5px}
.sign-in{position:absolute;left:982px;top:51px;width:83px;height:33px;background:var(--blue);border:1px solid #6cc0ec;
  border-radius:3px;color:var(--white);font-family:"Montserrat",sans-serif;font-weight:700;font-size:13px;
  display:flex;align-items:center;justify-content:center}
.menu{position:absolute;left:1078px;top:58px}
.tabs{position:absolute;left:98px;top:296px;width:1002px;height:42px;border-bottom:1px solid var(--blue);display:flex}
.tab{height:42px;display:flex;align-items:center;justify-content:center;font-size:16px;font-weight:600;color:#555;text-transform:uppercase}
.tab--active{width:207px;background:var(--blue);color:var(--white)}
.tab--events{width:205px;margin-left:0}
.tab--briefings{width:172px}
.panel{position:absolute;left:98px;top:338px;width:1002px;height:381px;background:var(--panel);border:1px solid var(--line);border-top:none}
.label{position:absolute;font-size:13.5px;color:var(--muted)}
.field{position:absolute;width:348px;height:35px;background:var(--white);border:1px solid #ddd;border-radius:2px}
.field::after{content:"";position:absolute;right:34px;top:0;bottom:0;border-left:1px solid #eee}
.field--select{font-size:11px;color:#777;padding-left:11px;display:flex;align-items:center}
.caret{position:absolute;right:12px;top:15px}
.submit{position:absolute;left:49px;top:276px;width:128px;height:37px;background:var(--blue);color:var(--white);
  font-size:15px;display:flex;align-items:center;justify-content:center;border-radius:1px}
.sources{position:absolute;left:426px;top:79px;width:348px;height:172px;background:var(--white);border:1px solid #ccc;border-radius:2px}
.sources__head{height:35px;border-bottom:1px solid #ccc;display:flex;align-items:center;padding-left:16px;font-size:11px;color:#777;gap:10px}
.sources__list{list-style:none;padding:14px 0 0 16px}
.sources__list li{height:22.6px;display:flex;align-items:center;gap:10px;font-size:12px;color:#555}
.check{width:10px;height:10px;flex:none}
.scroll{position:absolute;right:2px;top:38px;width:14px;height:130px}
.footer{position:absolute;left:0;top:785px;width:1200px;height:111px;background:var(--footer);border-top:1px solid #e6e6e6}
.footer__nav{position:absolute;left:99px;top:37px;font-size:12.5px;color:var(--blue);display:flex;gap:13px}
.footer__nav span.sep{color:#333}
.copyright{position:absolute;left:98px;top:63px;font-size:12.5px;color:#333}
.social{position:absolute;left:927px;top:35px;display:flex;gap:8px}
.social span{width:28px;height:28px;border-radius:50%;background:var(--blue);display:block}
</style>
</head>
<body>
<div class="page">
  <header class="hero" role="img" aria-label="Dusk aerial photograph of a city skyline with towers and lit streets">
    <div class="brand">BRIEFLY LEDGER</div>
    <div class="sign-in">SIGN IN</div>
    <svg class="menu" width="23" height="19" viewBox="0 0 23 19" aria-label="Menu">
      <rect y="0" width="23" height="3.5" fill="#fff"/><rect y="7.7" width="23" height="3.5" fill="#fff"/><rect y="15.5" width="23" height="3.5" fill="#fff"/>
    </svg>
  </header>

  <nav class="tabs">
    <div class="tab tab--active">Press Headlines</div>
    <div class="tab tab--events">Events</div>
    <div class="tab tab--briefings">Briefings</div>
  </nav>

  <section class="panel">
    <div class="label" style="left:49px;top:61px">Keywords :</div>
    <div class="field" style="left:49px;top:79px"></div>
    <div class="label" style="left:49px;top:130px">Authors :</div>
    <div class="field" style="left:49px;top:147px"></div>
    <div class="label" style="left:49px;top:199px">Date range :</div>
    <div class="field field--select" style="left:49px;top:216px">Past 24 hours
      <svg class="caret" width="8" height="5" viewBox="0 0 8 5"><path d="M0 0h8L4 5z" fill="#555"/></svg>
    </div>
    <div class="submit">SUBMIT</div>

    <div class="label" style="left:426px;top:61px">All Sources :</div>
    <div class="sources">
      <div class="sources__head">
        <svg class="check" viewBox="0 0 10 10"><rect x=".5" y=".5" width="9" height="9" fill="#fff" stroke="#999"/><path d="M2 5l2 2 4-5" stroke="#333" stroke-width="1.4" fill="none"/></svg>
        All Sources
      </div>
      <ul class="sources__list">
        <li><svg class="check" viewBox="0 0 10 10"><rect x=".5" y=".5" width="9" height="9" fill="#fff" stroke="#999"/><path d="M2 5l2 2 4-5" stroke="#333" stroke-width="1.4" fill="none"/></svg>Capitol Courier</li>
        <li><svg class="check" viewBox="0 0 10 10"><rect x=".5" y=".5" width="9" height="9" fill="#fff" stroke="#999"/><path d="M2 5l2 2 4-5" stroke="#333" stroke-width="1.4" fill="none"/></svg>Metro Daily Record</li>
        <li><svg class="check" viewBox="0 0 10 10"><rect x=".5" y=".5" width="9" height="9" fill="#fff" stroke="#999"/><path d="M2 5l2 2 4-5" stroke="#333" stroke-width="1.4" fill="none"/></svg>Ledgerline</li>
        <li><svg class="check" viewBox="0 0 10 10"><rect x=".5" y=".5" width="9" height="9" fill="#fff" stroke="#999"/><path d="M2 5l2 2 4-5" stroke="#333" stroke-width="1.4" fill="none"/></svg>The Sentinel's</li>
        <li><svg class="check" viewBox="0 0 10 10"><rect x=".5" y=".5" width="9" height="9" fill="#fff" stroke="#999"/><path d="M2 5l2 2 4-5" stroke="#333" stroke-width="1.4" fill="none"/></svg>Harbor Times</li>
      </ul>
      <svg class="scroll" viewBox="0 0 14 130">
        <rect width="14" height="130" fill="#f1f1f1"/>
        <path d="M4 8h6L7 4z" fill="#777"/>
        <rect x="3" y="12" width="8" height="36" fill="#b5b5b5"/>
        <path d="M4 122h6l-3 4z" fill="#777"/>
      </svg>
    </div>
  </section>

  <footer class="footer">
    <nav class="footer__nav"><span>ABOUT US</span><span class="sep">/</span><span>PRESS</span><span class="sep">/</span><span>CONTACT US</span></nav>
    <p class="copyright">2016 © Copyrights BRIEFLY ledger.All Rights Reserved</p>
    <div class="social" aria-label="Social links">
      <span aria-label="Social link"></span><span aria-label="Social link"></span><span aria-label="Social link"></span><span aria-label="Social link"></span><span aria-label="Social link"></span>
    </div>
  </footer>
</div>
</body>
</html>
```